Visualisation Software brochure

i need a sales brochure for a new visualisation software company called Lumora Studio Max.
The software has been specifically designed for manufacturers, distributers and retailers in the design / décor / furnishing / building industries. It allows customers can then import unlimited numbers of digital photos of rooms from their own home or take advantage of a library of pre-made photos, and then render different products from your catalogue into that photo to see what the finished look will be.
i have attached:
1) a mock up of the home page of the website
2) example of brochure wording that i have put together (although i am a little unsure about what other words i can add - so any suggestions here would be good)
3) i have attached some examples of other brochures that i like and would like similar designs
I am after a classy brochure used by a large corporate technology company that is given to executives and gives an impression of quality, trustworthiness and innovation.
• the colour blue as per the colours on my website mock up provided in the design brief
• I like simple, smart, clean and uncluttered design
• I like simple, clean and uncluttered design
• I like pictures that fit in with my technology (whether that be home and interior design, mixing virtual world and real world, visualising an idea) rather than basic stock of corporate people
Updates
Target Market(s)
marketing professionals
Industry/Entity Type
Software
Font styles to use
Look and feel
Each slider illustrates characteristics of the customer's brand and the style your logo design should communicate.

```html
<!DOCTYPE html>
<html lang="en">
<head>
<meta charset="utf-8">
<title>Lumora Studio Max – Benefits</title>
<link rel="stylesheet" href="https://fonts.googleapis.com/css2?family=Roboto+Condensed:wght@300;400&display=swap">
<style>
  :root {
    --sky-top: #3e6fb8;
    --sky-low: #8fb0d8;
    --house-glow: #f2c25a;
    --tree-dark: #1a2a1c;
    --lawn: #3f6a2a;
    --panel: rgba(246, 246, 248, 0.84);
    --ink: #2c2c2e;
    --heading: #1e1e20;
  }
  * { box-sizing: border-box; margin: 0; padding: 0; }
  html, body { width: 848px; height: 1200px; overflow: hidden; }
  body { font-family: "Roboto Condensed", "Arial Narrow", sans-serif; color: var(--ink); }
  .page { position: relative; width: 848px; height: 1200px; overflow: hidden; }
  .hero-photo {
    position: absolute; inset: 0;
    background:
      radial-gradient(ellipse 260px 420px at 90px 520px, rgba(242,194,90,0.9), rgba(242,194,90,0) 100%),
      radial-gradient(ellipse 300px 380px at 760px 560px, rgba(26,42,28,0.95), rgba(26,42,28,0) 100%),
      linear-gradient(to bottom, var(--sky-top) 0%, var(--sky-low) 30%, #5a6a5c 55%, var(--lawn) 75%, #2a4a1e 100%);
  }
  .benefits-panel {
    position: absolute; left: 176px; top: 352px; width: 496px; height: 848px;
    background: var(--panel);
    padding: 50px 62px 0 61px;
  }
  .benefits-panel h2 {
    font-weight: 400; font-size: 19px; color: var(--heading);
    margin-bottom: 13px;
  }
  .benefit-list { list-style: none; font-weight: 300; font-size: 12.6px; line-height: 16.8px; }
  .benefit-list li { position: relative; padding-left: 20px; }
  .benefit-list li::before {
    content: ""; position: absolute; left: 1px; top: 6px;
    width: 4px; height: 4px; border-radius: 50%; background: var(--ink);
  }
  .benefit-list--justified li { text-align: justify; }
  .consumer-section { margin-top: 97px; }
  .consumer-section h2 { margin-bottom: 16px; }
</style>
</head>
<body>
<main class="page">
  <div class="hero-photo" role="img" aria-label="Modern two-storey glass house lit warmly at dusk, with deep blue sky, dark trees and a green lawn"></div>

  <section class="benefits-panel">
    <div class="retailer-section">
      <h2>Retailer Benefits:</h2>
      <ul class="benefit-list">
        <li>Be the market innovator and leader by combining technology and a dynamic, seamless, integrated and consistent level of customer service across all online, bricks-and-mortar and mobile channels that delivers the big wow factor</li>
        <li>Extend your reach - don’t limit your technology footprint by only using Pomelo apps - our solution leverages and optimises all mobile devices and desktops (PomOS, Droidline, Web). This equates to a larger watershed of customers and more sales</li>
        <li>Increase brand engagement as our bespoke and scalable visualisation application will help customers build a relationship with your company, brand, and products and then share that experience within their social circles</li>
        <li>Understand buyer behaviour by receiving real usage statistics to obtain valuable insight about your customers and conduct trend analysis to determine how your future strategies can further enhance your bottom-line</li>
        <li>Increased sales to further grow your business</li>
        <li>Maximise the exposure of your products by uploading your entire product catalogue into a visualisation software that makes them look real</li>
      </ul>
    </div>

    <div class="consumer-section">
      <h2>Consumer Benefits:</h2>
      <ul class="benefit-list benefit-list--justified">
        <li>Reduce your customer’s purchase anxiety as they will have the knowledge that the products they are choosing from your range are the right choice</li>
        <li>Greater flexibility in the way they shop by being open 24/7 and being able to engage with your brand when they want and how they want. Happier customers and hence more sales.</li>
        <li>An easy-to-use interface along with guided help and tutorials for those less confident with technology</li>
        <li>Being able to make informed purchasing decisions as they can easily compare a large range of your products at the touch of a computer key</li>
        <li>Improved personalised buying experience by enabling customers to use photos of their own personal spaces and incorporate your products</li>
      </ul>
    </div>
  </section>
</main>
</body>
</html>
```